Want a package created for a new protein bar

We would like a new package created for a new protein bar project The name of the bar will be VORNBar a real food protein bar, we would like a ‘window’ on the package of bar like Bold Meadow bar below in images.

VORNBar
‘Super Food Bar’
14g of Whey Protein
The package film size is the following 12cm width x 15cm Length,
Flavor Peanut Chocolate Chip, additional information will be attached shortly like nutrition facts,

Target Market(s)

fitness market, bodybuilders, athletes, everyday people

Industry/Entity Type

Health Product

Logo Text

VORNBar

Font styles to use
Serif
Sans Serif
Decorative

Requirements
Must have
• Package window

```html
<!DOCTYPE html>
<html lang="en">
<head>
<meta charset="utf-8">
<title>VORNBar – Peanut Chocolate Chip Wrapper</title>
<link rel="stylesheet" href="https://fonts.googleapis.com/css2?family=Poppins:ital,wght@0,700;0,800;1,800;1,900&family=Montserrat:wght@500&display=swap">
<style>
  :root {
    --page-bg: #1d1d1d;
    --crimp: #181818;
    --crimp-ridge: #2c2c2c;
    --band-black: #0e0e0e;
    --band-dark: #151515;
    --silver: #c9c9cc;
    --panel-top: #6a6a6c;
    --panel-bottom: #2e2e30;
    --white: #f4f4f4;
    --gold: #9a7b2e;
    --accent-red: #b3141c;
    --oat-light: #e3c291;
    --oat-mid: #b98650;
    --oat-dark: #6e4122;
  }
  * { margin: 0; padding: 0; box-sizing: border-box; }
  html, body { width: 1200px; height: 1200px; overflow: hidden; background: var(--page-bg); }
  body { position: relative; font-family: "Poppins", sans-serif; }

  .wrapper {
    position: absolute; left: 40px; top: 380px; width: 1120px; height: 420px;
    background: linear-gradient(180deg, var(--panel-top) 0%, #505052 55%, var(--panel-bottom) 100%);
    overflow: hidden;
  }
  .top-strip { position: absolute; left: 80px; top: 0; width: 960px; height: 200px; background: var(--band-black); }
  .brand-band {
    position: absolute; left: 423px; top: 33px; width: 617px; height: 158px;
    background: linear-gradient(180deg, #1f1f20 0%, var(--band-dark) 60%, #050505 100%);
  }
  .silver-rule {
    position: absolute; left: 423px; top: 191px; width: 617px; height: 7px;
    background: linear-gradient(90deg, #8a8a8c, var(--silver) 50%, #8a8a8c);
  }
  .crimp {
    position: absolute; top: 0; width: 80px; height: 420px;
    background: repeating-linear-gradient(180deg, var(--crimp) 0 6px, var(--crimp-ridge) 6px 8px);
  }
  .crimp--left { left: 0; }
  .crimp--right { right: 0; }

  .product-window {
    position: absolute; left: 90px; top: 3px; width: 333px; height: 278px;
    background:
      radial-gradient(ellipse at 30% 30%, rgba(227,194,145,0.9) 0%, rgba(227,194,145,0) 45%),
      radial-gradient(ellipse at 70% 65%, rgba(110,65,34,0.55) 0%, rgba(110,65,34,0) 50%),
      linear-gradient(160deg, var(--oat-light) 0%, var(--oat-mid) 55%, var(--oat-dark) 100%);
  }
  .cookie-visual {
    position: absolute; left: 258px; top: 228px; width: 170px; height: 66px; border-radius: 50%;
    background: radial-gradient(ellipse at 55% 45%, #c0874a 0%, #8a5228 70%, #4a2a14 100%);
  }

  .brand-mark { position: absolute; left: 455px; top: 80px; width: 80px; height: 80px; border-radius: 50%; background: var(--accent-red); }
  .brand-name {
    position: absolute; left: 562px; top: 64px;
    font-family: "Poppins", sans-serif; font-weight: 800; font-size: 86px; line-height: 1;
    color: var(--white); letter-spacing: 1px;
  }
  .gold-lines { position: absolute; left: 0; top: 0; width: 1120px; height: 420px; pointer-events: none; }

  .tagline {
    position: absolute; left: 437px; top: 222px;
    font-family: "Montserrat", sans-serif; font-weight: 500; font-size: 19px;
    letter-spacing: 3.4px; color: var(--white); white-space: nowrap;
  }
  .flavor {
    position: absolute; left: 113px; top: 301px;
    font-family: "Poppins", sans-serif; font-weight: 800; font-style: italic; font-size: 26px;
    line-height: 1.2; color: var(--white); white-space: nowrap;
  }

  .claims {
    position: absolute; left: 674px; top: 303px; width: 338px; height: 44px;
    display: flex; border: 2px solid var(--white); border-radius: 8px;
  }
  .claim {
    flex: 1; display: flex; flex-direction: column; align-items: center; justify-content: center;
    border-right: 2px solid var(--white); color: var(--white);
    font-family: "Poppins", sans-serif; font-weight: 800; font-style: italic; line-height: 0.95;
  }
  .claim:last-child { border-right: none; }
  .claim__value { font-size: 19px; }
  .claim__value small { font-size: 11px; }
  .claim__label { font-size: 9.5px; text-transform: uppercase; }
  .claim--single .claim__label { font-size: 10px; text-align: center; }

  .tear-line {
    position: absolute; left: 0; top: 370px; width: 1120px; height: 0;
    border-top: 1px dashed var(--accent-red);
  }
</style>
</head>
<body>
  <div class="wrapper">
    <div class="top-strip"></div>
    <div class="brand-band"></div>
    <div class="silver-rule"></div>

    <svg class="gold-lines" viewBox="0 0 1120 420" aria-hidden="true">
      <line x1="890" y1="40" x2="800" y2="190" stroke="var(--gold)" stroke-width="1.2"/>
      <line x1="1010" y1="10" x2="880" y2="190" stroke="var(--gold)" stroke-width="1.2"/>
      <line x1="940" y1="25" x2="1040" y2="60" stroke="var(--gold)" stroke-width="1"/>
    </svg>

    <div class="product-window" role="img" aria-label="Close-up of the oat, peanut and chocolate chip bar through the package window"></div>
    <div class="cookie-visual" role="img" aria-label="Chocolate chip cookies"></div>

    <div class="brand-mark"></div>
    <div class="brand-name">VORNBAR</div>

    <p class="tagline">Snack with High Protein | Super food bar</p>
    <p class="flavor">Peanut Chocolate Chip</p>

    <div class="claims">
      <div class="claim"><span class="claim__value">14<small>g</small></span><span class="claim__label">Whey<br>Protein</span></div>
      <div class="claim"><span class="claim__value">120</span><span class="claim__label">Calories</span></div>
      <div class="claim"><span class="claim__value">5.25<small>g</small></span><span class="claim__label">Protein</span></div>
      <div class="claim claim--single"><span class="claim__label">Glutten<br>Free</span></div>
    </div>

    <div class="tear-line"></div>
    <div class="crimp crimp--left"></div>
    <div class="crimp crimp--right"></div>
  </div>
</body>
</html>
```